Glen Whitmore Professional Coaching

I would like a website with a mountain theme geared towards professional executives reaching higher peaks and goals. This is a 3 page website with brand essence information on the opening page, the coaching process on a second page and "about me" and lead capture form on a third page

Target Market(s)

C-Level audience, involved in tech, government, manufacturing, and transportation type of corporations

Coding

Coded - Design and coding required

Number of Pages Required

3 page

Font styles to use
Sans Serif

Colors
a7a7a7
1b1b1b
e8e8e8
3176b5
abd036
0355a3

Requirements
Must have
• Looking for a user friendly site that I can manage/update going forward. Must have:
• 1. "Is coaching right for you?" - page 1
• 2. "Our Process" page 2 - I will describe how we approach coaching
• 3. "Contact us" page 3 where I can capture contact information from potential clients
• 4. Clean and professional with more modern font
• 5. Links to personal social media sites
• 6. Ability to upload/download .pdf documents as resources
• 7. Ability to add on new pages in the future (such as a blog page)
Nice to have
• I want a place to store articles I write or use.
• Crestnet or Summit Feed Feed
Should not have
• Not fluffy or too 'zen' like personal life coaches tend to present.

```html
<!DOCTYPE html>
<html lang="en">
<head>
<meta charset="utf-8">
<title>Glen Whitmore Professional Coaching</title>
<link rel="stylesheet" href="https://fonts.googleapis.com/css2?family=Montserrat:wght@500;600;700&family=Open+Sans:wght@400;600;700&display=swap">
<style>
:root{
  --brand:#3a63c8;
  --brand-deep:#1c45c4;
  --brand-dark:#1a3a9e;
  --ink:#1b1b1b;
  --muted:#a7a7a7;
  --line:#e8e8e8;
  --white:#ffffff;
}
*{margin:0;padding:0;box-sizing:border-box}
html,body{width:1200px;height:3056px;overflow:hidden}
body{position:relative;background:var(--white);font-family:"Open Sans",Arial,sans-serif;color:var(--ink)}
.abs{position:absolute}
.heading{font-family:"Montserrat",Arial,sans-serif;font-weight:600;text-transform:uppercase}

/* header */
.site-header{left:0;top:0;width:1200px;height:131px;background:var(--brand);color:var(--white)}
.brand-name{left:90px;top:40px;font-size:34px;letter-spacing:.5px}
.contact-chip{top:20px;display:flex;align-items:center;gap:14px;font-size:14px;line-height:21px}
.contact-chip strong{font-weight:700;display:block}
.main-nav{left:436px;top:91px;display:flex;font-family:"Montserrat",Arial,sans-serif;font-size:15px;font-weight:500}
.main-nav a{color:var(--white);text-decoration:none;margin-right:36px}
.social-top{left:1000px;top:94px;display:flex;gap:12px;font-size:11px;font-weight:600;white-space:nowrap}

/* buttons */
.btn{display:flex;align-items:center;justify-content:center;gap:10px;background:linear-gradient(var(--brand-deep),var(--brand-dark));color:var(--white);font-family:"Montserrat",Arial,sans-serif;font-weight:600;font-size:17px;text-transform:uppercase;border-bottom:3px solid #132f85}

/* hero */
.hero-title{left:101px;top:265px;color:var(--white);text-shadow:0 2px 6px rgba(0,0,0,.25)}
.hero-title .small{font-size:32px;line-height:44px;display:block}
.hero-title .big{font-size:44px;line-height:62px;display:block}

/* about */
.about-title{left:550px;top:892px;font-size:34px;color:var(--brand)}
.about-text{left:550px;top:940px;width:565px;font-size:15px;line-height:31px;text-align:justify}

/* coaching */
.process-title{left:0;top:1545px;width:1200px;text-align:center;color:var(--white);font-size:32px}
.process-text{left:170px;top:1598px;width:860px;text-align:center;color:var(--white);font-size:15px;line-height:30px}
.process-card{top:1695px;width:306px;height:210px;box-shadow:0 4px 10px rgba(0,0,0,.25)}
.process-card .photo{width:306px;height:173px}
.process-card .label{height:37px;background:linear-gradient(var(--brand-deep),var(--brand-dark));color:var(--white);font-weight:700;font-size:18px;text-align:center;line-height:36px}

/* contact */
.contact-title{left:0;top:2116px;width:1200px;text-align:center;font-size:32px;color:var(--brand)}
.info-item{top:2196px;width:300px;text-align:center;font-size:17px;font-weight:600}
.info-item .circle{width:86px;height:86px;border-radius:50%;margin:0 auto 12px;background:linear-gradient(var(--brand),var(--brand-dark));border:3px solid #d9e0f4;display:flex;align-items:center;justify-content:center}
.info-item .value{margin-top:6px;font-size:17px}
.field{height:44px;border:1px solid var(--line);box-shadow:inset 0 1px 3px rgba(0,0,0,.08);font-size:12px;color:#444;padding:0 18px;display:flex;align-items:center;gap:8px;background:var(--white)}
.field.message{align-items:flex-start;padding-top:14px}

/* footer */
.footer-name{left:0;top:2828px;width:1200px;text-align:center;color:var(--white);font-size:42px}
.footer-nav{left:0;top:2912px;width:1200px;display:flex;justify-content:center;color:var(--white);font-family:"Montserrat",Arial,sans-serif;font-size:15px;font-weight:500}
.footer-nav span.sep{margin:0 24px}
.footer-social{left:0;top:2956px;width:1200px;display:flex;justify-content:center;gap:26px;color:var(--white);font-size:12px;font-weight:600}
.footer-social span{display:flex;align-items:center;gap:6px}
.footer-social i{display:inline-block;width:24px;height:24px;border:2px solid var(--white);border-radius:50%}
.copyright{left:0;top:3010px;width:1200px;text-align:center;color:var(--white);font-size:14px}
</style>
</head>
<body>

<header class="abs site-header">
  <div class="abs brand-name heading">Glen Whitmore</div>
  <div class="abs contact-chip" style="left:722px">
    <svg width="40" height="40" viewBox="0 0 40 40"><circle cx="20" cy="20" r="18" fill="none" stroke="#fff" stroke-width="2.5"/><path d="M13 11c2-1 3 0 4 3s-1 3-1 4c1 3 3 5 6 6 1 0 2-2 4-1s4 2 3 4-3 3-5 3c-8-1-14-7-15-14 0-2 2-4 4-5z" fill="#fff"/></svg>
    <div><strong>Call us:</strong>555 014 2290</div>
  </div>
  <div class="abs contact-chip" style="left:920px">
    <svg width="46" height="32" viewBox="0 0 46 32"><rect x="2" y="2" width="42" height="28" fill="none" stroke="#fff" stroke-width="2.5"/><path d="M2 2l21 17 21-17M2 30l15-13M44 30L29 17" fill="none" stroke="#fff" stroke-width="2.5"/></svg>
    <div><strong>Mail us:</strong>hello@glenwhitmore.com</div>
  </div>
  <nav class="abs main-nav"><a>HOME</a><a>ABOUT ME</a><a>COACHING PROCESS</a><a>CONTACT</a></nav>
  <div class="abs social-top"><span>Peakbook</span><span>Ridgeshot</span><span>Summit Feed</span></div>
</header>

<!-- hero -->
<svg class="abs" style="left:0;top:131px" width="1200" height="651" viewBox="0 131 1200 651">
  <defs>
    <linearGradient id="heroBase" x1="0" y1="0" x2="0" y2="1">
      <stop offset="0" stop-color="#c4bca6"/>
      <stop offset=".35" stop-color="#8f9484"/>
      <stop offset=".65" stop-color="#55625c"/>
      <stop offset="1" stop-color="#221f1d"/>
    </linearGradient>
    <radialGradient id="heroGlow" cx=".62" cy=".18" r=".55">
      <stop offset="0" stop-color="#efe6cf" stop-opacity=".75"/>
      <stop offset="1" stop-color="#efe6cf" stop-opacity="0"/>
    </radialGradient>
    <radialGradient id="heroShade" cx=".05" cy=".95" r=".7">
      <stop offset="0" stop-color="#1a1b22" stop-opacity=".8"/>
      <stop offset="1" stop-color="#1a1b22" stop-opacity="0"/>
    </radialGradient>
    <clipPath id="heroClip"><path d="M0 131H1200V668L1100 680 1000 690 900 700 790 700 690 720 600 762 530 738 450 735 360 712 240 700 120 690 0 668Z"/></clipPath>
  </defs>
  <g clip-path="url(#heroClip)" role="img" aria-label="Photo of a hiker standing on a rocky summit above misty mountain ranges">
    <rect x="0" y="131" width="1200" height="651" fill="url(#heroBase)"/>
    <rect x="0" y="131" width="1200" height="651" fill="url(#heroGlow)"/>
    <rect x="0" y="131" width="1200" height="651" fill="url(#heroShade)"/>
  </g>
  <path d="M0 672L120 694 240 704 360 716 450 739 530 742 600 768 690 724 790 704 900 704 1000 694 1100 684 1200 672" fill="none" stroke="var(--brand)" stroke-width="6"/>
</svg>
<h1 class="abs hero-title heading">
  <span class="small">Welcome to</span>
  <span class="big">Glen Whitmore</span>
  <span class="big">Professional Coaching</span>
</h1>
<div class="abs btn" style="left:101px;top:466px;width:178px;height:48px">
  <svg width="18" height="18" viewBox="0 0 18 18"><path d="M17 1L1 8l6 2 2 6z" fill="#fff"/></svg>Contact Us
</div>

<!-- about -->
<svg class="abs" style="left:80px;top:870px" width="450" height="390" viewBox="0 0 450 390">
  <defs>
    <radialGradient id="portraitFill" cx=".5" cy=".35" r=".7">
      <stop offset="0" stop-color="#8fa56a"/>
      <stop offset=".55" stop-color="#3f6233"/>
      <stop offset="1" stop-color="#1f2d3f"/>
    </radialGradient>
  </defs>
  <polygon points="110,4 340,4 446,195 340,386 110,386 4,195" fill="none" stroke="var(--brand)" stroke-width="3"/>
  <polygon role="img" aria-label="Portrait photo of the coach in a navy blazer outdoors" points="120,18 330,18 428,195 330,372 120,372 22,195" fill="url(#portraitFill)"/>
</svg>
<h2 class="abs about-title heading">About Me</h2>
<p class="abs about-text">At vero eos et accusamus et iusto odio dignissimos ducimus qui blanditiis praesentium voluptatum deleniti atque corrupti quos dolores et quas molestias excepturi sint occaecati cupiditate non provident, similique sunt in culpa qui officia deserunt mollitia animi, id est laborum et dolorum fuga. Et harum quidem rerum facilis est et expedita distinctio. Nam libero tempore, cum soluta nobis est eligendi optio cumque nihil impedit quo minus id quod maxime placeat facere possimus, omnis voluptas assumenda est, omnis dolor repellendus.</p>
<div class="abs btn" style="left:550px;top:1175px;width:180px;height:50px">
  <svg width="18" height="18" viewBox="0 0 18 18"><path d="M17 1L1 8l6 2 2 6z" fill="#fff"/></svg>Read More
</div>

<!-- coaching process -->
<svg class="abs" style="left:0;top:1340px" width="1200" height="678" viewBox="0 1340 1200 678">
  <defs>
    <linearGradient id="bandBase" x1="0" y1="0" x2="0" y2="1">
      <stop offset="0" stop-color="#8594c8"/>
      <stop offset=".25" stop-color="#6d86cc"/>
      <stop offset=".45" stop-color="#4c6bc0"/>
      <stop offset=".7" stop-color="#5a78c8"/>
      <stop offset="1" stop-color="#4f6fc6"/>
    </linearGradient>
    <radialGradient id="bandMist" cx=".5" cy=".3" r=".6">
      <stop offset="0" stop-color="#c9d3ef" stop-opacity=".55"/>
      <stop offset="1" stop-color="#c9d3ef" stop-opacity="0"/>
    </radialGradient>
    <clipPath id="bandClip"><path d="M0 1450L130 1430 260 1420 360 1400 480 1382 600 1352 700 1385 800 1395 900 1420 1050 1432 1200 1450V2018H0Z"/></clipPath>
  </defs>
  <g clip-path="url(#bandClip)" role="img" aria-label="Misty blue mountain range backdrop">
    <rect x="0" y="1340" width="1200" height="678" fill="url(#bandBase)"/>
    <rect x="0" y="1340" width="1200" height="678" fill="url(#bandMist)"/>
  </g>
  <path d="M0 1446L130 1426 260 1416 360 1396 480 1378 600 1348 700 1381 800 1391 900 1416 1050 1428 1200 1446" fill="none" stroke="var(--brand)" stroke-width="6"/>
</svg>
<h2 class="abs process-title heading">Coaching Process</h2>
<p class="abs process-text">Sed ut perspiciatis unde omnis iste natus error sit voluptatem accusantium doloremque laudantium, totam rem aperiam, eaque ipsa quae ab illo inventore veritatis et quasi architecto beatae vitae dicta sunt explicabo.</p>
<div class="abs process-card" style="left:112px">
  <div class="photo" role="img" aria-label="Photo of a wooden figure climbing wooden steps" style="background:radial-gradient(circle at 65% 60%,#e0a878 0,rgba(224,168,120,0) 55%),linear-gradient(160deg,#5e2c1b,#9a5634 55%,#c98a5c)"></div>
  <div class="label">Sed ut perspiciatis</div>
</div>
<div class="abs process-card" style="left:446px">
  <div class="photo" role="img" aria-label="Photo of metal gears engraved with career words" style="background:radial-gradient(circle at 45% 50%,#b9b9b2 0,rgba(185,185,178,0) 50%),linear-gradient(135deg,#2a2a2a,#6f6f6a 60%,#3c3c3a)"></div>
  <div class="label">Sed ut perspiciatis</div>
</div>
<div class="abs process-card" style="left:781px">
  <div class="photo" role="img" aria-label="Photo of a team meeting around a whiteboard" style="background:radial-gradient(circle at 40% 70%,#c79a80 0,rgba(199,154,128,0) 45%),linear-gradient(135deg,#8d8178,#d6d1ca 55%,#f0eeea)"></div>
  <div class="label">Sed ut perspiciatis</div>
</div>

<!-- contact -->
<h2 class="abs contact-title heading">Contact Us</h2>
<div class="abs info-item" style="left:153px">
  <div class="circle"><svg width="40" height="44" viewBox="0 0 40 44"><path d="M20 4a11 11 0 0 1 11 11c0 8-11 19-11 19S9 23 9 15A11 11 0 0 1 20 4z" fill="none" stroke="#fff" stroke-width="2.5"/><circle cx="20" cy="15" r="4" fill="none" stroke="#fff" stroke-width="2.5"/><ellipse cx="20" cy="38" rx="14" ry="4" fill="none" stroke="#fff" stroke-width="2"/></svg></div>
  <div>Location:</div><div class="value">2210 Ridge Lane, Denver, USA</div>
</div>
<div class="abs info-item" style="left:437px">
  <div class="circle"><svg width="40" height="40" viewBox="0 0 40 40"><path d="M12 6c3-1 4 1 5 4s-1 4-2 5c1 4 4 7 8 9 1 0 3-2 5-1s5 3 4 5-3 4-6 4C16 31 9 24 8 15c0-3 2-7 4-9z" fill="none" stroke="#fff" stroke-width="2.5"/></svg></div>
  <div>Phone:</div><div class="value">555 014 2290</div>
</div>
<div class="abs info-item" style="left:806px">
  <div class="circle"><svg width="44" height="32" viewBox="0 0 44 32"><rect x="2" y="2" width="40" height="28" fill="none" stroke="#fff" stroke-width="2.5"/><path d="M2 2l20 16 20-16M2 30l14-12M42 30L28 18" fill="none" stroke="#fff" stroke-width="2.5"/></svg></div>
  <div>Email:</div><div class="value">hello@glenwhitmore.com</div>
</div>

<form class="abs" style="left:0;top:0">
  <div class="abs field" style="left:162px;top:2395px;width:430px">&#9679; First Name</div>
  <div class="abs field" style="left:162px;top:2450px;width:430px">&#9632; Company</div>
  <div class="abs field" style="left:162px;top:2505px;width:430px">&#9993; Email Address</div>
  <div class="abs field" style="left:162px;top:2560px;width:430px">&#9990; Phone Number</div>
  <div class="abs field" style="left:610px;top:2395px;width:430px">&#9679; Last Name</div>
  <div class="abs field message" style="left:610px;top:2450px;width:430px;height:154px">&#9679; Message :</div>
  <div class="abs btn" style="left:511px;top:2615px;width:179px;height:48px">
    <svg width="18" height="18" viewBox="0 0 18 18"><path d="M17 1L1 8l6 2 2 6z" fill="#fff"/></svg><span style="text-transform:none">Submit</span>
  </div>
</form>

<!-- footer -->
<svg class="abs" style="left:0;top:2730px" width="1200" height="326" viewBox="0 2730 1200 326">
  <defs>
    <linearGradient id="footFill" x1="0" y1="0" x2="0" y2="1">
      <stop offset="0" stop-color="#9aa3c6"/>
      <stop offset=".45" stop-color="#6f7aa6"/>
      <stop offset=".75" stop-color="#3f4866"/>
      <stop offset="1" stop-color="#1b2030"/>
    </linearGradient>
  </defs>
  <path role="img" aria-label="Layered misty mountains with a dark pine forest" d="M0 2822L150 2792 300 2772 450 2752 600 2742 700 2757 850 2777 1000 2792 1200 2822V3056H0Z" fill="url(#footFill)"/>
  <path d="M0 2818L150 2788 300 2768 450 2748 600 2738 700 2753 850 2773 1000 2788 1200 2818" fill="none" stroke="var(--brand)" stroke-width="6"/>
</svg>
<div class="abs footer-name heading">Glen Whitmore</div>
<nav class="abs footer-nav"><span>HOME</span><span class="sep">|</span><span>ABOUT ME</span><span class="sep">|</span><span>COACHING PROCESS</span><span class="sep">|</span><span>CONTACT</span></nav>
<div class="abs footer-social">
  <span><i></i>Summit Feed</span><span><i></i>Peakbook</span><span><i></i>Crestnet</span><span><i></i>Trailhub</span>
</div>
<div class="abs copyright">© 2019 Company Name&nbsp; All right reserved</div>

</body>
</html>
```